Design a compelling Tarnwove Business Card that will drive people to my site

I want a business card that I can give to people—less to tell them who I am and more to direct them to my website. My website is a portal for Pelmor Aquatics Officials and a place for people who want to become Pelmor Aquatics Officials.
I am uploading my official company logo as well as a business card mockup that I did on my own. Please feel free to completely stray from this design.
I've included a screen recording of the homepage of my website as well.
Target Market(s)
Pelmor Aquatics Officials and people who desire to become one
Contact Information for Business Card
website url
Look and feel
Each slider illustrates characteristics of the customer's brand and the style your logo design should communicate.

```html
<!DOCTYPE html>
<html lang="en">
<head>
<meta charset="utf-8">
<title>Tarnwove Business Card</title>
<link rel="stylesheet" href="https://fonts.googleapis.com/css2?family=Montserrat:wght@400;500;700&display=swap">
<style>
  :root {
    --brand-blue: #3a55a8;
    --soft-blue: #a9b9e6;
    --card-white: #ffffff;
    --stage: #e8e9ed;
    --ink-light: #eef2ff;
  }
  * { box-sizing: border-box; margin: 0; padding: 0; }
  html, body {
    width: 1200px;
    height: 915px;
    overflow: hidden;
  }
  body {
    background: var(--stage);
    font-family: "Montserrat", sans-serif;
    position: relative;
  }
  .card {
    position: absolute;
    left: 250px;
    width: 700px;
    height: 400px;
    border-radius: 22px;
    overflow: hidden;
    box-shadow: 0 6px 18px rgba(0, 0, 0, 0.18);
  }
  .card-front {
    top: 40px;
    background: var(--brand-blue);
    display: flex;
    align-items: center;
    justify-content: center;
  }
  .card-back {
    top: 475px;
    display: flex;
  }
  .brand-name {
    font-weight: 700;
    letter-spacing: -1px;
    display: flex;
    align-items: center;
    gap: 14px;
  }
  .brand-name .dot {
    border-radius: 50%;
    flex: none;
  }
  .card-front .brand-name {
    color: var(--card-white);
    font-size: 84px;
  }
  .card-front .brand-name .dot {
    width: 30px;
    height: 30px;
    background: var(--card-white);
  }
  .back-brand-panel {
    width: 50%;
    background: var(--card-white);
    display: flex;
    align-items: center;
    justify-content: center;
  }
  .back-brand-panel .brand-name {
    color: var(--brand-blue);
    font-size: 52px;
  }
  .back-brand-panel .brand-name .dot {
    width: 20px;
    height: 20px;
    background: var(--brand-blue);
  }
  .back-contact-panel {
    width: 50%;
    background: var(--brand-blue);
    padding: 96px 0 0 48px;
    color: var(--ink-light);
  }
  .person-name {
    font-size: 27px;
    font-weight: 700;
    color: var(--soft-blue);
  }
  .person-title {
    font-size: 17px;
    font-weight: 500;
    margin-top: 4px;
  }
  .divider {
    width: 22px;
    height: 1px;
    background: var(--soft-blue);
    margin: 14px 0 16px;
  }
  .contact-list { list-style: none; }
  .contact-item {
    display: flex;
    align-items: center;
    gap: 12px;
    font-size: 17px;
    font-weight: 500;
    margin-bottom: 12px;
  }
  .contact-icon {
    width: 24px;
    height: 24px;
    flex: none;
  }
</style>
</head>
<body>
  <section class="card card-front" aria-label="Card front">
    <div class="brand-name"><span class="dot"></span>tarnwove</div>
  </section>

  <section class="card card-back" aria-label="Card back">
    <div class="back-brand-panel">
      <div class="brand-name"><span class="dot"></span>tarnwove</div>
    </div>
    <div class="back-contact-panel">
      <h1 class="person-name">Daniel Morrow</h1>
      <p class="person-title">CEO &amp; Founder</p>
      <div class="divider"></div>
      <ul class="contact-list">
        <li class="contact-item">
          <svg class="contact-icon" viewBox="0 0 24 24" aria-hidden="true">
            <circle cx="12" cy="12" r="11" fill="none" stroke="#a9b9e6" stroke-width="1.2"/>
            <path d="M8.5 7.5l2 2-1.2 1.3a6 6 0 0 0 3.9 3.9l1.3-1.2 2 2-1.4 1.4c-3.6 0-8-4.4-8-8z" fill="#a9b9e6"/>
          </svg>
          (555) 201-4417
        </li>
        <li class="contact-item">
          <svg class="contact-icon" viewBox="0 0 24 24" aria-hidden="true">
            <circle cx="12" cy="12" r="11" fill="none" stroke="#a9b9e6" stroke-width="1.2"/>
            <rect x="6.5" y="8" width="11" height="8" rx="1" fill="#a9b9e6"/>
            <path d="M6.5 8.5l5.5 4 5.5-4" fill="none" stroke="#3a55a8" stroke-width="1"/>
          </svg>
          dan@tarnwove.com
        </li>
        <li class="contact-item">
          <svg class="contact-icon" viewBox="0 0 24 24" aria-hidden="true">
            <circle cx="12" cy="12" r="11" fill="none" stroke="#a9b9e6" stroke-width="1.2"/>
            <circle cx="12" cy="12" r="6" fill="none" stroke="#a9b9e6" stroke-width="1.2"/>
            <path d="M6 12h12M12 6c-2.5 3.5-2.5 8.5 0 12M12 6c2.5 3.5 2.5 8.5 0 12" fill="none" stroke="#a9b9e6" stroke-width="1"/>
          </svg>
          www.tarnwove.com
        </li>
      </ul>
    </div>
  </section>
</body>
</html>
```